CREATE A 2 layout and logo ( servanilo )

I need to create 2 layout for my company being a homepage will be like and other client control panel and need to create the logo of the company, my company works with website hosting and sale of dedicated server and VPS cloud the company name and servanilo, I want the site to be very accessible and that is not too flashy

Target Market(s)

website hosting

Industry/Entity Type

It Company

Number of Pages Required

2 page

Font styles to use
Sans Serif

Requirements
Must have
• domain servanilo.example
Nice to have
• banners, login area, login webmail
Should not have
• no preference

```html
<!DOCTYPE html>
<html lang="en">
<head>
<meta charset="utf-8">
<title>Servanilo — Hosting, Dedicated Servers, VPS Cloud</title>
<link href="https://fonts.googleapis.com/css2?family=Open+Sans:ital,wght@0,400;0,600;0,700;1,400&display=swap" rel="stylesheet">
<style>
:root{
  --brand:#1f5bb5;
  --ink:#333;
  --muted:#555;
  --nav:#666;
  --band:#efefed;
  --footer:#3b3b3b;
  --footer-deep:#2f2f2f;
  --white:#fff;
  --hero-top:#3d6fa8;
  --hero-bottom:#a9c8e4;
}
*{margin:0;padding:0;box-sizing:border-box}
html,body{width:868px;height:1200px;overflow:hidden;background:var(--white)}
body{font-family:"Open Sans",Arial,sans-serif;color:var(--ink);position:relative}
.abs{position:absolute}
.topline{left:0;top:0;width:868px;height:2px;background:var(--brand)}
.logo{left:72px;top:26px;font-size:20px;font-weight:600;color:var(--brand);letter-spacing:.5px}
.nav a{position:absolute;top:35px;font-size:9px;color:var(--nav);text-decoration:none}
.lang{left:665px;top:30px;width:62px;height:22px;border:1px solid #555;border-radius:2px;font-size:7px;color:#333;padding:6px 0 0 7px}
.lang .flag{display:inline-block;width:11px;height:7px;background:#2a3f8f;vertical-align:-1px;margin-right:5px}
.login{left:735px;top:30px;width:62px;height:22px;border:1px solid var(--brand);border-radius:2px;font-size:9px;color:#333;text-align:center;line-height:21px}
.hero{left:0;top:78px;width:868px;height:334px;background:linear-gradient(180deg,var(--hero-top),var(--hero-bottom))}
.hero-arrow{top:233px}
.welcome{left:0;width:868px;top:436px;text-align:center;font-size:17px;font-weight:700;color:#3a3a3a}
.welcome span{color:var(--brand)}
.intro{left:0;width:868px;top:467px;text-align:center;font-size:8px;line-height:20px;color:var(--muted)}
.card-img{top:547px;width:219px;height:131px;box-shadow:4px 4px 6px rgba(0,0,0,.15)}
.card h3{position:absolute;top:693px;font-size:9px;font-weight:700;color:#222}
.card p{position:absolute;top:711px;width:230px;font-size:8px;line-height:17px;color:var(--muted);white-space:nowrap}
.band{left:0;top:786px;width:868px;height:192px;background:var(--band)}
.sec-title{top:808px;font-size:13px;font-weight:700;color:var(--brand)}
.about-text{left:71px;top:836px;width:400px;font-size:8px;line-height:16.3px;color:var(--muted);white-space:nowrap}
.btn-primary{left:71px;top:928px;width:97px;height:26px;background:var(--brand);color:#fff;font-size:8px;text-align:center;line-height:26px;border-radius:2px}
.avatar{left:508px;top:846px;width:76px;height:76px;border-radius:50%;background:#8a8f99}
.quote{left:621px;top:853px;width:170px;font-size:7.5px;font-style:italic;line-height:14.3px;color:var(--muted);white-space:nowrap}
.qmark{font-size:20px;color:#bbb;font-family:Georgia,serif}
.t-name{left:621px;top:918px;font-size:8px;font-weight:700;color:#444}
.t-sub{left:621px;top:932px;font-size:8px;color:var(--muted)}
.footer{left:0;top:978px;width:868px;height:187px;background:var(--footer)}
.footbar{left:0;top:1165px;width:868px;height:35px;background:var(--footer-deep);color:#ddd;font-size:8px;text-align:center;line-height:34px}
.fcol{top:1005px;color:#fff}
.fcol h4{font-size:9px;font-weight:700;margin-bottom:6px}
.fcol li{list-style:none;font-size:8px;line-height:16.7px}
.fcol p{font-size:8px;margin-bottom:10px}
.input{width:182px;height:22px;background:#fff;border-radius:2px;font-size:7.5px;color:#888;padding:6px 10px}
.btn-dark{margin-top:9px;width:101px;height:24px;background:#222;color:#fff;font-size:8px;font-weight:700;text-align:center;line-height:24px;border-radius:2px}
.social li{display:flex;align-items:center;height:30px;font-size:8px}
.social .dot{width:20px;height:20px;border-radius:50%;background:#fff;margin-right:5px}
</style>
</head>
<body>
<div class="abs topline"></div>
<div class="abs logo">SERVANILO</div>
<nav class="nav">
  <a style="left:398px">HOME</a>
  <a style="left:458px">ABOUT US</a>
  <a style="left:533px">CONTACT US</a>
  <a style="left:618px">HELP</a>
</nav>
<div class="abs lang"><span class="flag"></span>English ▾</div>
<div class="abs login">LOG IN</div>

<div class="abs hero" role="img" aria-label="Banner photo: server racks framing a sky over clouds"></div>
<svg class="abs hero-arrow" style="left:22px" width="18" height="18" viewBox="0 0 18 18"><circle cx="9" cy="9" r="9" fill="rgba(255,255,255,.55)"/><path d="M10.5 5 6.5 9l4 4" fill="none" stroke="#555" stroke-width="2"/></svg>
<svg class="abs hero-arrow" style="left:828px" width="18" height="18" viewBox="0 0 18 18"><circle cx="9" cy="9" r="9" fill="rgba(255,255,255,.55)"/><path d="M7.5 5l4 4-4 4" fill="none" stroke="#555" stroke-width="2"/></svg>

<h1 class="abs welcome">WELCOME TO <span>SERVANILO</span></h1>
<p class="abs intro">On the other hand, we denounce with righteous indignation and dislike men who are so beguiled and demoralized by the charms of pleasure of the moment, so blinded<br>by desire, that they cannot foresee the pain and trouble that are bound to ensue; and equal blame belongs to those who fail in their duty through<br>weakness of will, which is the same as saying through shrinking from toil and pain.</p>

<section class="card">
  <div class="abs card-img" style="left:71px;background:#3f6aa3" role="img" aria-label="Photo of a data centre aisle"></div>
  <h3 style="left:71px">WEBSITE HOSTING</h3>
  <p style="left:72px">At vero eos et accusamus et iusto odio dignissimos duci-<br>mus qui blanditiis praesentium voluptatum deleniti<br>dolo dolorum fuga distinctio.,</p>
</section>
<section class="card">
  <div class="abs card-img" style="left:324px;background:#8c8c8c" role="img" aria-label="Photo of a dedicated server rack"></div>
  <h3 style="left:324px">DEDICATED SERVER</h3>
  <p style="left:325px">At vero eos et accusamus et iusto odio dignissimos duci-<br>mus qui blanditiis praesentium voluptatum deleniti<br>dolo dolorum fuga distinctio.,</p>
</section>
<section class="card">
  <div class="abs card-img" style="left:577px;background:#2a3d55" role="img" aria-label="Illustration for VPS cloud service"></div>
  <h3 style="left:577px">VPS CLOUD</h3>
  <p style="left:578px">At vero eos et accusamus et iusto odio dignissimos duci-<br>mus qui blanditiis praesentium voluptatum deleniti<br>dolo dolorum fuga distinctio.,</p>
</section>

<div class="abs band"></div>
<h2 class="abs sec-title" style="left:71px">ABOUT US</h2>
<p class="abs about-text">Lorem Ipsum es simplemente el texto de relleno de las imprentas y archivos de texto. Lorem Ipsum ha<br>sido el texto de relleno estándar de las industrias desde el año 1500, cuando un impresor (N. del T. per-<br>sona que se dedica a la imprenta) desconocido usó una galería de textos y los mezcló de tal manera que<br>logró hacer un libro de textos especimen. No sólo sobrevivió 500 años, sino que tambien ingresó como<br>texto de relleno en documentos electrónicos...</p>
<div class="abs btn-primary">READ MORE INFO</div>

<h2 class="abs sec-title" style="left:506px">TESTIMONIALS</h2>
<svg class="abs" style="left:774px;top:812px" width="16" height="10" viewBox="0 0 16 10"><path d="M4 2 1 5l3 3M12 2l3 3-3 3" fill="none" stroke="#999" stroke-width="1"/></svg>
<div class="abs avatar" role="img" aria-label="Portrait photo of a client"></div>
<span class="abs qmark" style="left:602px;top:846px">“</span>
<p class="abs quote">Lorem Ipsum es simplemente el texto de<br>relleno de las imprentas y archivos de texto.<br>Lorem Ipsum ha sido el texto de relleno<br>estándar de las...</p>
<span class="abs qmark" style="left:782px;top:892px">”</span>
<div class="abs t-name">ON THE OTHER HAND</div>
<div class="abs t-sub">We denounce</div>

<footer>
  <div class="abs footer"></div>
  <div class="abs fcol" style="left:71px"><h4>INFORMATION</h4><ul><li>Home</li><li>About Us</li><li>Products</li><li>Services</li><li>Online Shop</li><li>Contact us</li></ul></div>
  <div class="abs fcol" style="left:211px"><h4>PRODUCTS</h4><ul><li>On the other</li><li>Hand, we denounce</li><li>Righteous</li><li>Indignation</li><li>Dislike</li></ul></div>
  <div class="abs fcol" style="left:344px"><h4>INFORMATION</h4><ul><li>Search</li><li>Blog</li><li>About Us</li><li>Contact us</li></ul></div>
  <div class="abs fcol" style="left:475px"><h4>NEWSLETTER SIGNUP</h4><p>Get our recent updates through your email id</p><div class="input">Enter your email id</div><div class="btn-dark">LOGIN WEBMAIL</div></div>
  <div class="abs fcol social" style="left:710px"><h4>FOLLOW US</h4><ul><li><span class="dot"></span>: Friendwall</li><li><span class="dot"></span>: Chirpline</li><li><span class="dot"></span>: Workmesh</li></ul></div>
  <div class="abs footbar">© 2015. Servanilo. All Rights Reserved.</div>
</footer>
</body>
</html>
```